Facial Tissue Brand Logo and Design

We would like you to design a Logo for the Facial Tissue Brand "Velora" along with the box design. The pack should indicate the pack size (150 x 2 ply). Also our company logo should be present (attached) along with a barcode. The box size dimensions should be 210mm (L) x 110mm (W) x 70mm (H). We are open to all kinds of nice designs which are attractive but not overdone. Happy designing!

UPDATE:
We appreciate the designs so far... but would also love to see more options in a simple and elegent design style that would look good on a table... please see attached below links for reference purpose:

www.pictovault-example.com/image-photo/cleaning-wipes-isolated-on-white-257770819

www.pictovault-example.com/image-photo/cleaning-wipes-isolated-on-white-155326937

www.pictovault-example.com/image-photo/delicate-female-hands-pulling-tissue-out-1330426586

Happy desgining!

We appreciate the designs so far.. but would like to to see some more options.

```html
<!DOCTYPE html>
<html lang="en">
<head>
<meta charset="utf-8">
<title>Velora Facial Tissue – Box Dieline</title>
<link rel="stylesheet" href="https://fonts.googleapis.com/css2?family=Montserrat:wght@400;500&display=swap">
<style>
  :root {
    --backdrop: #b8e4fd;
    --brand-blue: #1a6fa3;
    --deep-blue: #0c4a73;
    --mid-blue: #2a80b8;
    --pale: #e9eff4;
    --flap-light: #fbfbfc;
    --flap-grey: #e3e6e9;
    --fold-line: #8fb6d3;
    --dim-red: #e0323a;
    --white: #ffffff;
  }
  html, body {
    margin: 0;
    width: 1200px;
    height: 1200px;
    overflow: hidden;
    background: var(--backdrop);
  }
  .dieline-canvas {
    display: block;
    width: 1200px;
    height: 1200px;
    font-family: "Montserrat", sans-serif;
  }
  .brand-name { font-weight: 400; letter-spacing: 2px; }
  .brand-name--blue { fill: var(--brand-blue); }
  .brand-name--white { fill: var(--white); }
  .pack-title { font-size: 8.5px; font-weight: 400; }
  .pack-size { font-size: 6.5px; font-weight: 500; }
  .pack-text--white { fill: var(--white); }
  .pack-text--blue { fill: var(--brand-blue); }
  .company-name { font-size: 7.5px; fill: var(--mid-blue); font-weight: 400; }
  .company-country { font-size: 2.6px; fill: #7d8a96; letter-spacing: 1.2px; }
  .fold-line { stroke: var(--fold-line); stroke-width: 0.7; stroke-dasharray: 8 6; fill: none; }
  .dimension-line { stroke: var(--dim-red); stroke-width: 0.7; stroke-dasharray: 5 4; fill: none; }
  .dimension-label { fill: var(--dim-red); font-size: 9px; font-weight: 400; }
</style>
</head>
<body>
<svg class="dieline-canvas" viewBox="0 0 1200 1200" xmlns="http://www.w3.org/2000/svg">
  <defs>
    <linearGradient id="panel-fill" x1="0" y1="212" x2="0" y2="948" gradientUnits="userSpaceOnUse">
      <stop offset="0" stop-color="#0d4f7c"/>
      <stop offset="0.16" stop-color="#1a6fa6"/>
      <stop offset="0.3" stop-color="#6fa7cd"/>
      <stop offset="0.38" stop-color="#e6edf3"/>
      <stop offset="0.55" stop-color="#ffffff"/>
      <stop offset="0.72" stop-color="#dce7ef"/>
      <stop offset="0.8" stop-color="#5fa0cb"/>
      <stop offset="0.9" stop-color="#1a6ea5"/>
      <stop offset="1" stop-color="#0b4670"/>
    </linearGradient>
    <linearGradient id="flap-fill" x1="0" y1="0" x2="1" y2="1">
      <stop offset="0" stop-color="var(--flap-grey)"/>
      <stop offset="0.5" stop-color="var(--flap-light)"/>
      <stop offset="1" stop-color="var(--flap-grey)"/>
    </linearGradient>
    <filter id="sheet-shadow" x="-20%" y="-20%" width="140%" height="140%">
      <feDropShadow dx="0" dy="0" stdDeviation="14" flood-color="#2f7fb3" flood-opacity="0.55"/>
    </filter>
  </defs>

  <!-- box sheet -->
  <g class="box-sheet" filter="url(#sheet-shadow)">
    <rect class="neck" x="404" y="445" width="433" height="135" fill="#eceef0"/>
    <path class="neck" d="M404 800 L837 800 L837 940 L404 940 Z" fill="#dfe3e6"/>
    <path class="flap flap--left-top" d="M271 218 L415 212 L415 453 L271 448 Q265 448 265 442 L265 224 Q265 218 271 218 Z" fill="url(#flap-fill)"/>
    <path class="flap flap--right-top" d="M831 212 L976 218 Q982 218 982 224 L982 442 Q982 448 976 448 L831 453 Z" fill="url(#flap-fill)"/>
    <path class="flap flap--left-bottom" d="M271 574 L415 568 L415 810 L271 804 Q265 804 265 798 L265 580 Q265 574 271 574 Z" fill="url(#flap-fill)"/>
    <path class="flap flap--right-bottom" d="M831 568 L976 574 Q982 574 982 580 L982 798 Q982 804 976 804 L831 810 Z" fill="url(#flap-fill)"/>
    <path class="main-panel" role="img" aria-label="Low-poly faceted pattern in blue and white" d="M415 212 L831 212 L831 807 L837 807 L837 942 Q837 948 831 948 L416 948 Q410 948 410 942 L410 807 L415 807 Z" fill="url(#panel-fill)"/>
  </g>

  <!-- fold lines -->
  <g class="fold-lines">
    <line class="fold-line" x1="278" y1="224" x2="969" y2="224"/>
    <line class="fold-line" x1="278" y1="442" x2="969" y2="442"/>
    <line class="fold-line" x1="278" y1="580" x2="969" y2="580"/>
    <line class="fold-line" x1="278" y1="797" x2="969" y2="797"/>
    <line class="fold-line" x1="415" y1="935" x2="831" y2="935"/>
    <line class="fold-line" x1="278" y1="224" x2="278" y2="442"/>
    <line class="fold-line" x1="969" y1="224" x2="969" y2="442"/>
    <line class="fold-line" x1="278" y1="580" x2="278" y2="797"/>
    <line class="fold-line" x1="969" y1="580" x2="969" y2="797"/>
  </g>

  <!-- dispensing opening -->
  <rect class="dispenser-opening" x="483" y="648" width="280" height="82" rx="41" fill="#ffffff" fill-opacity="0.75" stroke="#9bbbd4" stroke-width="0.7" stroke-dasharray="3 2"/>

  <!-- top panel -->
  <text class="brand-name brand-name--blue" x="623" y="519" font-size="21" text-anchor="middle" transform="rotate(180 623 512)">VELORA</text>
  <g class="pack-label pack-text--blue" transform="rotate(180 795 460)">
    <text class="pack-title" x="765" y="458">Facial Tissue</text>
    <text class="pack-size" x="765" y="467">150 x 2 ply</text>
  </g>
  <text class="brand-name brand-name--blue" x="778" y="615" font-size="12" text-anchor="middle">VELORA</text>
  <g class="pack-label pack-text--white">
    <text class="pack-title" x="425" y="779">Facial Tissue</text>
    <text class="pack-size" x="425" y="788">150 x 2 ply</text>
  </g>

  <!-- front panel -->
  <text class="brand-name brand-name--white" x="623" y="884" font-size="20" text-anchor="middle">VELORA</text>
  <g class="pack-label pack-text--white">
    <text class="pack-title" x="425" y="917">Facial Tissue</text>
    <text class="pack-size" x="425" y="926">150 x 2 ply</text>
  </g>

  <!-- side flaps -->
  <text class="brand-name brand-name--blue" x="342" y="340" font-size="19" text-anchor="middle" transform="rotate(-90 342 333)">VELORA</text>
  <text class="brand-name brand-name--blue" x="905" y="340" font-size="19" text-anchor="middle" transform="rotate(90 905 333)">VELORA</text>

  <g class="company-mark" transform="rotate(90 363 686)">
    <rect x="322" y="672" width="8" height="8" fill="var(--mid-blue)"/>
    <text class="company-name" x="334" y="679">Norvale Trading FZC</text>
    <text class="company-country" x="334" y="690">UNITED ARAB EMIRATES</text>
  </g>
  <g class="company-mark" transform="rotate(-90 882 689)">
    <rect x="841" y="675" width="8" height="8" fill="var(--mid-blue)"/>
    <text class="company-name" x="853" y="682">Norvale Trading FZC</text>
    <text class="company-country" x="853" y="693">UNITED ARAB EMIRATES</text>
  </g>

  <!-- dimensions -->
  <g class="dimensions">
    <path class="dimension-line" d="M236 580 Q218 580 218 592 L218 785 Q218 797 236 797"/>
    <text class="dimension-label" x="231" y="691" text-anchor="middle" transform="rotate(-90 231 688)">110 mm</text>
    <path class="dimension-line" d="M362 807 Q336 815 336 830 L336 923 Q336 935 352 935"/>
    <text class="dimension-label" x="349" y="886" text-anchor="middle" transform="rotate(-90 349 883)">70 mm</text>
    <path class="dimension-line" d="M416 960 L416 980 Q416 987 426 987 L821 987 Q831 987 831 980 L831 960"/>
    <text class="dimension-label" x="623" y="983" text-anchor="middle">210 mm</text>
  </g>
</svg>
</body>
</html>
```